Redesign This Psychology Website

We would like a slight redesign of this successful psychology (relationship counselling) website:

www.TheKelvaleClinic.com.au

We are updating the website, and we'd like a slight refresh of the design and style.

Please keep to very similar colours, and use the same logo. We're looking for around 10 page templates, however the main one is the home page.

Keep in mind, this website already converts quite well, so we want a new, fresh design in keeping with this one. Please don't bother designing something too extremely different.

thanks :)

Target Market(s)

couples who are looking for relationship counselling. Men and women, 25 - 70, across Australia

Industry/Entity Type

Psychology

Number of Pages Required

5+ page

Font styles to use
Sans Serif

Colors
87cfc6
b7a5cd
ec1f27
ffffff
cee9f5

Requirements
Must have
• a similar look to the current design, just looking for a slight refresh.
• Search bar
• Areas for lots of photos
• same logo
• lots of content areas
Nice to have
• great content areas, where we can display a lot of content and our areas.
Should not have
• no colors like orange, etc.
• should not have a totally different feel.

```html
<!DOCTYPE html>
<html lang="en">
<head>
<meta charset="utf-8">
<title>Contact Us – The Kelvale Clinic</title>
<link rel="stylesheet" href="https://fonts.googleapis.com/css2?family=Lato:wght@400;700&family=Open+Sans:wght@400;600&display=swap">
<style>
:root{
  --teal:#87cfc6;
  --teal-dark:#6bbfb4;
  --teal-ink:#1f7f8d;
  --purple:#b7a5cd;
  --red:#ec1f27;
  --white:#ffffff;
  --ink:#333333;
  --grey:#7a7a7a;
  --grey-light:#f0f0f0;
  --line:#d6d6d6;
}
*{box-sizing:border-box;margin:0;padding:0}
html,body{width:1200px;height:2419px;overflow:hidden;background:var(--white)}
body{position:relative;font-family:"Open Sans",Arial,sans-serif;color:var(--ink)}
ul{list-style:none}
.abs{position:absolute}

/* top bar */
.utility-bar{position:absolute;left:0;top:0;width:1200px;height:37px;background:var(--grey-light);border-bottom:1px solid #e2e2e2}
.utility-bar .associate{position:absolute;left:132px;top:9px;font-size:14px;color:#666}
.utility-links{position:absolute;right:206px;top:0;display:flex;height:37px}
.utility-links a{font-size:13px;color:#888;text-decoration:none;padding:0 12px;line-height:37px;border-left:1px solid #dcdcdc}
.utility-links a:first-child{border-left:none}

/* header */
.site-header{position:absolute;left:0;top:37px;width:1200px;height:124px;background:var(--white)}
.brand{position:absolute;left:116px;top:28px;display:flex;align-items:center;gap:10px}
.brand-dot{width:46px;height:46px;border-radius:50%;background:var(--teal-ink)}
.brand-name{font-family:"Lato",sans-serif;font-weight:400;font-size:28px;color:var(--teal-ink);line-height:1}
.brand-tagline{font-family:"Lato",sans-serif;font-size:13px;color:var(--teal-ink);margin-top:6px}
.search{position:absolute;left:458px;top:47px;width:353px;height:39px;border:1px solid #cfcfcf;border-radius:2px;display:flex;align-items:center;padding-left:10px;gap:8px;font-size:12px;color:#999}
.call{position:absolute;right:144px;top:38px;text-align:right}
.call-label{font-family:"Lato",sans-serif;font-size:16px;color:var(--teal)}
.call-number{font-family:"Lato",sans-serif;font-size:23px;color:var(--teal-ink);display:flex;align-items:center;gap:6px;margin-top:2px}

/* nav */
.main-nav{position:absolute;left:0;top:161px;width:1200px;height:67px;background:linear-gradient(#9bd9d1,#72c4b9)}
.main-nav li{position:absolute;top:0;height:67px;display:flex;align-items:center;font-family:"Lato",sans-serif;font-size:16px;line-height:17px;color:var(--white);text-transform:uppercase}
.nav-sep{position:absolute;top:0;width:1px;height:67px;background:rgba(255,255,255,.6)}

/* hero */
.hero{position:absolute;left:0;top:228px;width:1200px;height:325px;background:linear-gradient(100deg,#cfd3d6 0%,#b9c4cf 40%,#d9d4cf 70%,#c9c6c3 100%)}
.hero-title{position:absolute;left:126px;top:160px;font-family:"Lato",sans-serif;font-weight:700;font-size:38px;color:var(--white);letter-spacing:.5px}

/* intro */
.intro-name{position:absolute;left:135px;top:610px;font-family:"Lato",sans-serif;font-size:29px;color:#222}
.intro-phone{position:absolute;left:136px;top:661px;font-family:"Lato",sans-serif;font-size:29px;color:var(--teal-dark)}
.intro-note{position:absolute;left:136px;top:699px;font-family:"Lato",sans-serif;font-size:17px;color:#222}

/* forms */
.form-card{position:absolute;top:758px;width:458px;height:353px;color:var(--white)}
.form-card.appointment{left:127px;background:var(--teal)}
.form-card.enquiry{left:610px;background:var(--purple)}
.form-title{position:absolute;left:28px;top:28px;font-family:"Lato",sans-serif;font-weight:700;font-size:22px}
.field-label{position:absolute;font-size:13px}
.field{position:absolute;width:192px;height:31px;background:var(--white)}
.select{position:absolute;left:34px;top:237px;width:192px;height:33px;background:#f4f4f4;border:1px solid #ddd;font-size:11px;color:#666;padding-left:11px;line-height:31px}
.select svg{position:absolute;right:9px;top:12px}
.radio{position:absolute;left:246px;display:flex;align-items:center;gap:7px;font-size:12px}
.radio i{display:block;width:11px;height:11px;border-radius:50%;background:var(--white)}
.next-btn{position:absolute;left:34px;top:290px;width:142px;height:36px;background:linear-gradient(#f23a3f,#d8121a);font-family:"Lato",sans-serif;font-weight:700;font-size:17px;text-align:center;line-height:36px;color:var(--white)}

/* locations */
.locations-title{position:absolute;left:140px;top:1158px;font-family:"Lato",sans-serif;font-size:25px;color:var(--red)}
.location-list{position:absolute;top:1213px}
.location-list li{height:33.87px;display:flex;align-items:center;font-size:15px;color:var(--grey);line-height:15px}
.location-list li::before{content:"";display:inline-block;width:0;height:0;border-top:5px solid transparent;border-bottom:5px solid transparent;border-left:6px solid var(--teal);margin-right:7px;flex:none}
.location-list .two-line{font-size:14px;line-height:13px}

/* footer */
.site-footer{position:absolute;left:0;top:2048px;width:1200px;height:299px;background:linear-gradient(#e9e9e9,#ffffff 30%)}
.footer-brand{position:absolute;left:142px;top:78px}
.footer-col{position:absolute;top:72px}
.footer-col h3{font-family:"Lato",sans-serif;font-weight:700;font-size:16px;color:var(--teal-ink);margin-bottom:8px}
.footer-col li{font-size:12px;color:#555;line-height:27.4px}
.socials{position:absolute;left:832px;top:181px;display:flex;gap:6px}
.socials span{width:32px;height:32px;border-radius:50%}
.copyright-bar{position:absolute;left:0;top:2347px;width:1200px;height:72px;background:var(--grey-light);text-align:center;font-size:12px;color:#666;line-height:62px}
</style>
</head>
<body>

<div class="utility-bar">
  <span class="associate">Join Our Assoicate Program →</span>
  <nav class="utility-links"><a href="#">Home</a><a href="#">Cart</a><a href="#">Blog</a><a href="#">Resources</a><a href="#">Contact</a></nav>
</div>

<header class="site-header">
  <div class="brand">
    <span class="brand-dot"></span>
    <div>
      <div class="brand-name">The Kelvale Clinic</div>
      <div class="brand-tagline">helping you create loving relationships</div>
    </div>
  </div>
  <div class="search">
    <svg width="14" height="14" viewBox="0 0 14 14"><circle cx="6" cy="6" r="4.5" fill="none" stroke="#aaa" stroke-width="1.5"/><line x1="9.3" y1="9.3" x2="13" y2="13" stroke="#aaa" stroke-width="1.5"/></svg>
    Search here
  </div>
  <div class="call">
    <div class="call-label">Call Us Now</div>
    <div class="call-number">
      <svg width="22" height="22" viewBox="0 0 24 24"><path d="M6.6 10.8a15 15 0 0 0 6.6 6.6l2.2-2.2c.3-.3.7-.4 1-.2 1.1.4 2.3.6 3.6.6.6 0 1 .4 1 1V20c0 .6-.4 1-1 1A17 17 0 0 1 3 4c0-.6.4-1 1-1h3.5c.6 0 1 .4 1 1 0 1.3.2 2.5.6 3.6.1.3 0 .7-.2 1z" fill="none" stroke="#ec1f27" stroke-width="1.6"/></svg>
      1300 555 014
    </div>
  </div>
</header>

<nav class="main-nav">
  <ul>
    <li style="left:121px">Counselling<br>Types</li>
    <li style="left:261px">Relationship Counselling<br>Locations</li>
    <li style="left:531px">Sex Therapy<br>Locations</li>
    <li style="left:665px">About Us</li>
    <li style="left:777px">Quizzes</li>
    <li style="left:887px">FAQ's</li>
    <li style="left:968px">Contact</li>
  </ul>
  <span class="nav-sep" style="left:250px"></span>
  <span class="nav-sep" style="left:516px"></span>
  <span class="nav-sep" style="left:648px"></span>
  <span class="nav-sep" style="left:761px"></span>
  <span class="nav-sep" style="left:865px"></span>
  <span class="nav-sep" style="left:952px"></span>
</nav>

<section class="hero" role="img" aria-label="Photo of a smiling couple looking at a laptop together on a sofa">
  <h1 class="hero-title">CONTACT US</h1>
</section>

<h2 class="intro-name">The Kelvale Clinic</h2>
<p class="intro-phone">1300 555 014</p>
<p class="intro-note">and our friendly receptionists will help you</p>

<form class="form-card appointment">
  <h3 class="form-title">Request an Appointment</h3>
  <span class="field-label" style="left:34px;top:75px">First Name</span>
  <span class="field-label" style="left:242px;top:75px">Last Name</span>
  <span class="field" style="left:34px;top:100px"></span>
  <span class="field" style="left:242px;top:100px"></span>
  <span class="field-label" style="left:34px;top:143px">Phone</span>
  <span class="field-label" style="left:242px;top:143px">Email</span>
  <span class="field" style="left:34px;top:168px"></span>
  <span class="field" style="left:242px;top:168px"></span>
  <span class="field-label" style="left:34px;top:213px">Type of Counselling</span>
  <span class="field-label" style="left:246px;top:213px">I prefer to be contacted by*</span>
  <div class="select">Relationship Counselling<svg width="12" height="8" viewBox="0 0 12 8"><path d="M0 0h12L6 8z" fill="#999"/></svg></div>
  <span class="radio" style="top:243px"><i></i>Email</span>
  <span class="radio" style="top:267px"><i></i>Phone</span>
  <span class="next-btn">Next</span>
</form>

<form class="form-card enquiry">
  <h3 class="form-title">Email an Enquiry</h3>
  <span class="field-label" style="left:34px;top:75px">First Name</span>
  <span class="field-label" style="left:242px;top:75px">Last Name</span>
  <span class="field" style="left:34px;top:100px"></span>
  <span class="field" style="left:242px;top:100px"></span>
  <span class="field-label" style="left:34px;top:143px">Phone</span>
  <span class="field-label" style="left:242px;top:143px">Email</span>
  <span class="field" style="left:34px;top:168px"></span>
  <span class="field" style="left:242px;top:168px"></span>
  <span class="field-label" style="left:34px;top:213px">Type of Counselling</span>
  <span class="field-label" style="left:246px;top:213px">I prefer to be contacted by*</span>
  <div class="select">Relationship Counselling<svg width="12" height="8" viewBox="0 0 12 8"><path d="M0 0h12L6 8z" fill="#999"/></svg></div>
  <span class="radio" style="top:243px"><i></i>Email</span>
  <span class="radio" style="top:267px"><i></i>Phone</span>
  <span class="next-btn">Next</span>
</form>

<h2 class="locations-title">Our Location</h2>
<ul class="location-list" style="left:132px">
  <li>Adelaide</li><li>Unley</li><li>North Adelaide</li><li>Kensington</li><li>Modbury Heights</li><li>Brisbane</li>
  <li class="two-line">Brisbane CBD<br>(Wickham Tce &amp; Queen St)</li>
  <li>Carindale</li><li>Indooroopilly</li><li>Annerley</li><li>Auchenflower</li><li>Ashgrove</li><li>Oxley</li>
  <li>Chermside West</li><li>Sunnybank Hills</li><li>Deception Bay</li><li>Canberra</li><li>Phillip</li><li>Hughes</li><li>Cairns</li><li>Cairns CBD</li>
</ul>
<ul class="location-list" style="left:381px">
  <li>Central Coast</li><li>Erina</li><li>Gold Coast</li><li>Isle of Capri</li><li>Coomera</li><li>Southport</li><li>Miami</li>
  <li>Mermaid Beach Melbourne</li><li>Berwick</li><li>Tecoma (Belgrave)</li><li>Balwyn</li><li>Carlton Nth</li><li>Nunawading</li>
  <li>East Melbourne</li><li>Altona Meadows</li><li>Moonee Ponds</li><li>Frankston South</li><li>Armadale</li><li>Toorak</li><li>Preston</li><li>Carlton (Miriam)</li>
</ul>
<ul class="location-list" style="left:655px">
  <li>Melbourne CBD</li><li>Richmond</li><li>Hampton</li><li>Clifton Hill</li><li>Williamstown</li><li>Perth</li><li>Leeming</li>
  <li>Perth CBD</li><li>West Leederville</li><li>Midland</li><li>Mount Lawley</li><li>Heathridge</li><li>North Perth</li><li>Mandurah</li>
  <li>Ardross</li><li>Subiaco</li><li>Nedlands &nbsp;&nbsp;&nbsp;Sydney</li><li>Randwick</li><li>Five Dock</li><li>Dulwich Hill</li><li>Riverstone</li>
</ul>
<ul class="location-list" style="left:887px">
  <li>Green Square (Rosebery)</li><li>Caringbah</li><li>Bondi Junction</li><li>Parramatta</li><li>Mosman</li><li>Penrith</li>
  <li>Sydney CBD (George St)</li><li>Sydney CBD (Pitt St)</li><li>GlebeCrows Nest</li><li>Mona Vale</li><li>Windsor Downs</li>
  <li>Sunshine Coast</li><li>Maroochydore (Deborah)</li><li>Maroochydore (Annette)</li><li>Townsville</li><li>Rosslea</li>
  <li>Warner's Bay &amp; Newcastle</li><li>(Unavailable at present)</li><li>Wodonga</li><li>Wodonga</li><li>Wollongong</li><li>Wollongong</li>
</ul>

<footer class="site-footer">
  <div class="brand footer-brand" style="top:78px;left:142px">
    <span class="brand-dot"></span>
    <div>
      <div class="brand-name">The Kelvale Clinic</div>
      <div class="brand-tagline">helping you create loving relationships</div>
    </div>
  </div>
  <div class="footer-col" style="left:463px">
    <h3>QUICK LINKS</h3>
    <ul><li>Home</li><li>About Us</li><li>Our Blogs</li><li>Shop Cart</li><li>Contact Us</li></ul>
  </div>
  <div class="footer-col" style="left:629px">
    <h3>RESOURCES</h3>
    <ul><li>Counselling Type</li><li>Sex Therapy</li><li>Quizzes</li><li>FAQ</li><li>Relationship Counselling</li></ul>
  </div>
  <div class="footer-col" style="left:834px">
    <h3>CONTACT US</h3>
    <ul><li>42 Harbour View Road Suite 12</li><li>1300 555 014</li><li>Email: info@kelvaleclinic.com.au</li></ul>
  </div>
  <div class="socials">
    <span style="background:var(--teal)"></span>
    <span style="background:var(--teal-ink)"></span>
    <span style="background:var(--purple)"></span>
    <span style="background:var(--red)"></span>
  </div>
</footer>

<div class="copyright-bar">© 2017 Kelvale Clinic &nbsp;All right reserved</div>

</body>
</html>
```